Web Design Project

Update to the following web page.

www.velbrontadvisory.com

We would like a full screen website, similar to the ones found here. http://www.pixelorbit.com/websites/fullscreen/

We also really like this site
http://lumenfold.com/

We would like new images and graphics.

Menu should be
1. Audit Defense
2. Education
3. Consulting
4. Outsourcing
5. Our Team
6. Store
7. Contact Us

Incorporate our new logo and colors. File is attached. The blue logo.

We want to add this tag line: "A passion for compliance through homecare and hospice training, education, and consulting."

Target Market(s)

Home Health Care Companies

Industry/Entity Type

Defense

Requirements
Must have
• Display our contact information in header and footer.

```html
<!DOCTYPE html>
<html lang="en">
<head>
<meta charset="utf-8">
<title>Velbront Advisory</title>
<link rel="stylesheet" href="https://fonts.googleapis.com/css2?family=Montserrat:wght@400;500&family=Mulish:wght@400&display=swap">
<style>
  :root {
    --bg-deep: #0c1c26;
    --bg-mid: #2f5366;
    --panel: rgba(24, 40, 50, 0.82);
    --panel-line: rgba(255, 255, 255, 0.08);
    --text: #ffffff;
    --text-soft: #e6edf0;
    --text-dim: #9fb0b8;
    --footer: rgba(14, 26, 34, 0.92);
    --button: #0a0f12;
  }
  * { margin: 0; padding: 0; box-sizing: border-box; }
  html, body { width: 1200px; height: 750px; overflow: hidden; }
  body {
    position: relative;
    font-family: "Mulish", sans-serif;
    color: var(--text);
    background: var(--bg-deep);
  }
  .hero-photo {
    position: absolute; inset: 0;
    background:
      radial-gradient(ellipse 380px 260px at 880px 230px, rgba(160,185,196,0.55), transparent 70%),
      radial-gradient(ellipse 520px 360px at 420px 420px, rgba(90,125,142,0.5), transparent 75%),
      linear-gradient(160deg, var(--bg-mid) 0%, #1d3a4a 45%, var(--bg-deep) 100%);
  }
  .brand {
    position: absolute; left: 125px; top: 26px; height: 62px; width: 265px;
    display: flex; align-items: center;
  }
  .brand-mark { width: 40px; height: 40px; background: var(--text); margin: 0 53px 0 0; }
  .brand-divider { width: 1px; height: 62px; background: var(--text); opacity: .8; margin-right: 15px; }
  .brand-name {
    font-family: "Montserrat", sans-serif; font-weight: 400;
    font-size: 19px; line-height: 22px; letter-spacing: 1px; color: var(--text);
  }
  .social {
    position: absolute; top: 6px; left: 984px;
    display: flex; gap: 12px;
  }
  .social span { width: 13px; height: 13px; border-radius: 50%; background: var(--text); opacity: .85; }
  .main-nav {
    position: absolute; left: 399px; top: 27px; width: 675px; height: 62px;
    background: var(--panel); display: flex;
  }
  .main-nav a {
    flex: auto; display: flex; align-items: center; justify-content: center;
    font-family: "Montserrat", sans-serif; font-weight: 500; font-size: 12px;
    color: var(--text); text-decoration: none; letter-spacing: .2px;
    border-right: 1px solid var(--panel-line);
  }
  .main-nav a:last-child { border-right: 0; }
  .tagline {
    position: absolute; left: 131px; top: 244px; width: 700px;
    font-family: "Montserrat", sans-serif; font-weight: 500;
    font-size: 26px; line-height: 34px; letter-spacing: -0.3px; text-transform: uppercase;
    color: var(--text-soft);
  }
  .years-badge { position: absolute; left: 886px; top: 232px; }
  .card {
    position: absolute; top: 518px; height: 160px;
    background: var(--panel); padding: 20px 20px 0;
  }
  .card-about { left: 131px; width: 283px; }
  .card-coding { left: 457px; width: 284px; padding-left: 15px; padding-right: 22px; }
  .card h2 {
    font-family: "Mulish", sans-serif; font-weight: 400; font-size: 15px;
    margin-bottom: 13px; display: flex; align-items: center; gap: 12px;
  }
  .card-coding h2 { margin-top: -2px; }
  .card-icon { width: 26px; height: 26px; border-radius: 50%; background: #b9d4e6; }
  .card p { font-size: 10.4px; line-height: 14.5px; color: var(--text-soft); }
  .card-more {
    position: absolute; right: 0; bottom: -4px; width: 20px; height: 20px;
    background: var(--button); display: flex; align-items: center; justify-content: center;
  }
  .video { position: absolute; left: 790px; top: 518px; width: 284px; height: 160px; overflow: hidden; }
  .video-still {
    position: absolute; inset: 0;
    background: linear-gradient(180deg, #8aa6b8 0%, #c9d2d6 45%, #6f6a63 78%, #3c3a36 100%);
  }
  .video-bar {
    position: absolute; left: 0; right: 0; bottom: 0; height: 22px;
    background: rgba(0,0,0,.55);
    display: flex; align-items: center; gap: 8px; padding: 0 12px;
    font-size: 7.5px; color: var(--text);
  }
  .video-progress { position: absolute; left: 14px; right: 150px; bottom: 20px; height: 2px; background: rgba(255,255,255,.5); }
  .video-bar .spacer { flex: 1; }
  .footer {
    position: absolute; left: 0; right: 0; top: 710px; height: 40px;
    background: var(--footer);
  }
  .footer-nav { position: absolute; left: 153px; top: 14px; display: flex; gap: 9px; }
  .footer-nav a { font-size: 9px; color: var(--text-dim); text-decoration: none; }
  .copyright { position: absolute; left: 878px; top: 14px; font-size: 9px; color: var(--text-dim); }
</style>
</head>
<body>
  <div class="hero-photo" role="img" aria-label="Close-up of a stethoscope lying on a computer keyboard, tinted in deep blue"></div>

  <header>
    <div class="brand">
      <span class="brand-mark"></span>
      <span class="brand-divider"></span>
      <span class="brand-name">VELBRONT<br>ADVISORY</span>
    </div>
    <div class="social" aria-label="Social links"><span></span><span></span><span></span><span></span></div>
    <nav class="main-nav">
      <a href="#">AUDIT DEFENSE</a>
      <a href="#">EDUCATION</a>
      <a href="#">CONSULTING</a>
      <a href="#">OUTSOURCING</a>
      <a href="#">OUR TEAM</a>
      <a href="#">STORE</a>
      <a href="#">CONTACT US</a>
    </nav>
  </header>

  <h1 class="tagline">A passion for compliance<br>through homecare and hospice training,<br>education, and consulting.</h1>

  <svg class="years-badge" width="126" height="126" viewBox="0 0 126 126" aria-label="More than 25 years">
    <circle cx="63" cy="63" r="61" fill="none" stroke="#fff" stroke-opacity=".55" stroke-width="1.5"/>
    <circle cx="63" cy="63" r="55" fill="rgba(255,255,255,.06)" stroke="#fff" stroke-opacity=".8" stroke-width="2"/>
    <circle cx="63" cy="63" r="50" fill="none" stroke="#fff" stroke-opacity=".4" stroke-width="1"/>
    <circle cx="57" cy="36" r="1.6" fill="#fff"/><circle cx="69" cy="36" r="1.6" fill="#fff"/>
    <text x="63" y="54" text-anchor="middle" fill="#fff" font-family="Montserrat, sans-serif" font-size="11.5">MORE THAN</text>
    <text x="63" y="80" text-anchor="middle" fill="#fff" font-family="Montserrat, sans-serif" font-size="22" font-weight="500">25</text>
    <text x="63" y="97" text-anchor="middle" fill="#fff" font-family="Montserrat, sans-serif" font-size="11">YEARS</text>
  </svg>

  <section class="card card-about">
    <h2>About</h2>
    <p>With over 100 years of combined experience in home health care, we have compiled a very strong team of consultants to meet any challenge home health agencies may face today!</p>
    <a class="card-more" href="#"><svg width="8" height="10" viewBox="0 0 8 10"><path d="M2 1l4 4-4 4" fill="none" stroke="#fff" stroke-width="1.3"/></svg></a>
  </section>

  <section class="card card-coding">
    <h2><span class="card-icon"></span>Outsourcing coding</h2>
    <p>Outsourcing coding and QA will free up clinical staff so that they may focus on patient care and perform other clinical duties (review of revisit notes, formulating and periodic review of Plan of Care, follow up on orders, staff education, etc.)</p>
    <a class="card-more" href="#"><svg width="8" height="10" viewBox="0 0 8 10"><path d="M2 1l4 4-4 4" fill="none" stroke="#fff" stroke-width="1.3"/></svg></a>
  </section>

  <div class="video">
    <div class="video-still" role="img" aria-label="Video still of the white office building with a curved glass entrance"></div>
    <div class="video-progress"></div>
    <div class="video-bar">
      <svg width="8" height="9" viewBox="0 0 8 9"><path d="M1 0l7 4.5L1 9z" fill="#fff"/></svg>
      <svg width="9" height="9" viewBox="0 0 9 9"><path d="M7.5 4.5a3 3 0 1 1-1-2.2" fill="none" stroke="#fff" stroke-width="1.2"/><path d="M6 0.5l1.2 2-2.2.3z" fill="#fff"/></svg>
      <span>3:19 / 7:00</span>
      <span class="spacer"></span>
      <svg width="12" height="9" viewBox="0 0 12 9"><path d="M0 3h2l3-3v9L2 6H0z" fill="#fff"/><path d="M7 3l3 3M10 3l-3 3" stroke="#fff"/></svg>
      <svg width="28" height="4" viewBox="0 0 28 4"><rect width="28" height="2" y="1" fill="#fff"/></svg>
      <svg width="12" height="9" viewBox="0 0 12 9"><path d="M0 3h2l3-3v9L2 6H0z" fill="#fff"/><path d="M7 2.5q2 2 0 4M9 1q3.5 3.5 0 7" fill="none" stroke="#fff"/></svg>
      <svg width="9" height="9" viewBox="0 0 9 9"><path d="M0 0h3L0 3zM9 0v3L6 0zM0 9V6l3 3zM9 9H6l3-3zM2 2l5 5M7 2L2 7" fill="#fff" stroke="#fff" stroke-width=".8"/></svg>
    </div>
  </div>

  <footer class="footer">
    <nav class="footer-nav">
      <a href="#">Education</a><a href="#">Consulting</a><a href="#">Outsourcing</a><a href="#">Our Team</a><a href="#">Blog</a><a href="#">Store</a><a href="#">Resources</a><a href="#">Contact Us</a>
    </nav>
    <p class="copyright">© Velbront &amp; Associates, LLC ©2012</p>
  </footer>
</body>
</html>
```